Business Card Design

New business card design

Target Market(s)

Residential & Commercial Property Managers

Industry/Entity Type

Plumbing Services

Contact Information for Business Card

Name - Rowan Keddle, title - Director, Phone Number - 0431 286 517, email - rowan@tbk-plumbing.com.au, Company ABN - 73 215 904 386,

Font styles to use
Sans Serif

Colors
0054AA
0677BA
7BADD7
CADEEF
E8F1F8

```html
<!DOCTYPE html>
<html lang="en">
<head>
<meta charset="utf-8">
<title>TBK Plumbing Services – Business Card</title>
<link rel="stylesheet" href="https://fonts.googleapis.com/css2?family=Arimo:wght@400;700&display=swap">
<style>
  :root {
    --page: #d9d9d9;
    --card-blue: #05a3e3;
    --card-white: #f7f7f7;
    --ink: #1b252e;
    --paper-text: #ffffff;
  }
  * { margin: 0; padding: 0; box-sizing: border-box; }
  html, body {
    width: 1200px;
    height: 800px;
    overflow: hidden;
    background: var(--page);
    font-family: "Arimo", Arial, sans-serif;
  }
  .stage {
    position: relative;
    width: 1200px;
    height: 800px;
  }
  .card {
    position: absolute;
    left: 337px;
    width: 526px;
    height: 300px;
    border-radius: 22px;
    box-shadow: 0 10px 24px rgba(0,0,0,0.18);
    overflow: hidden;
  }
  .card--back { top: 60px; background: var(--card-blue); color: var(--paper-text); }
  .card--front {
    top: 420px;
    background: var(--card-white);
    display: flex;
    align-items: center;
    justify-content: center;
  }

  .brand {
    color: var(--ink);
    font-weight: 400;
    letter-spacing: 0.04em;
    line-height: 1;
    white-space: nowrap;
  }
  .card--back .brand {
    position: absolute;
    top: 58px;
    right: 40px;
    font-size: 30px;
  }
  .card--front .brand { font-size: 42px; }

  .divider {
    position: absolute;
    left: 32px;
    right: 32px;
    top: 196px;
    height: 1px;
    background: rgba(255,255,255,0.85);
  }
  .person {
    position: absolute;
    left: 40px;
    bottom: 112px;
  }
  .person__name {
    font-size: 22px;
    font-weight: 700;
    color: var(--ink);
    line-height: 1.1;
  }
  .person__role {
    font-size: 14px;
    margin-top: 3px;
  }
  .contact {
    position: absolute;
    left: 40px;
    top: 210px;
  }
  .contact__line {
    display: flex;
    align-items: center;
    gap: 8px;
    font-size: 15px;
    line-height: 1.45;
  }
  .contact__line svg { width: 12px; height: 12px; fill: var(--ink); flex: none; }
  .company {
    position: absolute;
    right: 40px;
    bottom: 112px;
    text-align right;
    text-align: right;
    font-size: 15px;
    line-height: 1.4;
  }
</style>
</head>
<body>
<main class="stage">
  <section class="card card--back" aria-label="Business card, contact side">
    <p class="brand">TBK Plumbing Services</p>
    <div class="person">
      <p class="person__name">Rowan Keddle</p>
      <p class="person__role">Director</p>
    </div>
    <div class="company">
      <p>ABN - 73 215 904 386</p>
      <p>www.tbk-plumbing.com</p>
    </div>
    <div class="divider"></div>
    <div class="contact">
      <p class="contact__line">
        <svg viewBox="0 0 24 24" aria-hidden="true"><path d="M6.6 10.8a15 15 0 0 0 6.6 6.6l2.2-2.2c.3-.3.7-.4 1-.2 1.1.4 2.3.6 3.6.6.6 0 1 .4 1 1V20c0 .6-.4 1-1 1A17 17 0 0 1 3 4c0-.6.4-1 1-1h3.5c.6 0 1 .4 1 1 0 1.3.2 2.5.6 3.6.1.3 0 .7-.2 1z"/></svg>
        0431 286 517
      </p>
      <p class="contact__line">
        <svg viewBox="0 0 24 24" aria-hidden="true"><path d="M2 5h20v14H2zm2 2v.5l8 5 8-5V7l-8 5z"/></svg>
        rowan@tbk-plumbing.com.au
      </p>
    </div>
  </section>

  <section class="card card--front" aria-label="Business card, name side">
    <p class="brand">TBK Plumbing Services</p>
  </section>
</main>
</body>
</html>
```